Copper lark buildworks

Copper lark buildworks is a small construction company.
Who is a licenced builder, Carpenter, joiner,
working on heritage ,new build, speacial projects and sometimes furniture

Industry/Entity Type

Construction

```html
<!DOCTYPE html>
<html lang="en">
<head>
<meta charset="utf-8">
<title>Copper lark buildworks – business card</title>
<link href="https://fonts.googleapis.com/css2?family=Montserrat:wght@400;500;700;800&display=swap" rel="stylesheet">
<style>
  :root {
    --page-bg: #e6e6e4;
    --card-white: #ffffff;
    --green-light: #4c8c0c;
    --green-dark: #3e7806;
    --green-accent: #5aa51a;
    --brand-green: #3d7a08;
    --stripe-grey: #353535;
    --panel-black: #000000;
    --text-white: #ffffff;
  }
  * { margin: 0; padding: 0; box-sizing: border-box; }
  html, body {
    width: 1200px; height: 1000px; overflow: hidden;
    background: var(--page-bg);
    font-family: "Montserrat", Arial, sans-serif;
  }
  .business-card {
    position: absolute; left: 150px; top: 240px;
    width: 900px; height: 520px;
    border-radius: 28px; overflow: hidden;
    background: var(--card-white);
    box-shadow: 0 10px 30px rgba(0,0,0,.18);
  }
  .card-shapes { position: absolute; inset: 0; width: 100%; height: 100%; }
  .brand-name {
    position: absolute; right: 60px; top: 42px;
    text-align: right;
    font-weight: 800; font-size: 50px; line-height: 1;
    letter-spacing: -1px; text-transform: uppercase;
    color: var(--brand-green);
  }
  .services {
    position: absolute; right: 34px; top: 214px;
    text-align: right; font-size: 20px; line-height: 1.2;
    color: var(--text-white);
  }
  .services .services-label { color: var(--green-accent); }
  .contact {
    position: absolute; left: 62px; top: 330px;
    color: var(--text-white);
  }
  .contact .person-name { font-weight: 700; font-size: 26px; line-height: 1.1; }
  .contact .person-role { font-size: 17px; margin-bottom: 22px; }
  .contact .address { font-size: 19px; margin-bottom: 4px; }
  .contact .line { display: flex; align-items: center; gap: 10px; font-size: 19px; line-height: 1.4; }
  .contact .icon { width: 18px; height: 18px; flex: none; }
</style>
</head>
<body>
  <section class="business-card">
    <svg class="card-shapes" viewBox="0 0 900 520" preserveAspectRatio="none" aria-hidden="true">
      <path fill="var(--green-light)" d="M0,225 Q400,345 900,140 L900,520 L0,520 Z"/>
      <path fill="var(--green-dark)" d="M0,300 Q430,375 900,175 L900,520 L0,520 Z"/>
      <path fill="var(--stripe-grey)" d="M735,150 Q590,320 545,520 L900,520 L900,130 Z"/>
      <path fill="var(--panel-black)" d="M765,140 Q620,320 580,520 L900,520 L900,120 Z"/>
      <path fill="var(--card-white)" d="M0,0 L900,0 L900,140 Q400,345 0,225 Z"/>
    </svg>

    <div class="brand-name">Copper lark<br>buildworks</div>

    <div class="services">
      <div class="services-label">working on</div>
      <div>heritage</div>
      <div>new build</div>
      <div>speacial projects</div>
      <div>and furniture</div>
    </div>

    <div class="contact">
      <div class="person-name">Martin Hale</div>
      <div class="person-role">Licenced Builder &amp; Carpenter</div>
      <div class="address">12 Harbour Lane Singapore 40512</div>
      <div class="line">
        <svg class="icon" viewBox="0 0 24 24"><path fill="#fff" d="M6.6 10.8a15 15 0 0 0 6.6 6.6l2.2-2.2a1 1 0 0 1 1-.25 11.4 11.4 0 0 0 3.6.57 1 1 0 0 1 1 1V20a1 1 0 0 1-1 1A17 17 0 0 1 3 4a1 1 0 0 1 1-1h3.5a1 1 0 0 1 1 1c0 1.25.2 2.45.57 3.57a1 1 0 0 1-.25 1z"/></svg>
        <span>0400555017</span>
      </div>
      <div class="line">
        <svg class="icon" viewBox="0 0 24 24"><rect x="2" y="5" width="20" height="14" rx="2" fill="#fff"/><path d="M3 6l9 7 9-7" fill="none" stroke="#3e7806" stroke-width="2"/></svg>
        <span>martin@copperlark.com</span>
      </div>
      <div class="line">
        <svg class="icon" viewBox="0 0 24 24"><circle cx="12" cy="12" r="10" fill="#fff"/><path d="M2 12h20M12 2c3 3 3 17 0 20M12 2c-3 3-3 17 0 20" fill="none" stroke="#3e7806" stroke-width="1.6"/></svg>
        <span>www.copperlark.com</span>
      </div>
    </div>
  </section>
</body>
</html>
```